New website for salon services and wedding hair and makeup

I am a professional hairstylist and makeup artist in Charleston, SC. I have my own company where I see clients for cut and color and I also go on site for weddings. I have a current website that I would like to update and change the style. I would like to add a contact form, map, additional pages and be mobile friendly. It is important to me that it have a site map and can show up in searches. I will need to add photos to the site every so often and would like to continue to work with the designer. I have a logo that I am happy with and have attached the file however if you think a new logo would help the look of the site I am open to it. My current website is www.brightcombstudio-example.com, I would like to change the style and layout so it looks up to date. Here are some links to sites that I like the look of but I don't want to limit your creativity. http://willowlanefolio-example.com/ http://www.runwaylensworks-example.com http://miraventhol-example.com/. I have attached a few files for mock up purposes, please let me know if you would like more content. Thank you!

Target Market(s)

Women, Brides

Industry/Entity Type

Hair And Beauty

Number of Pages Required

1 page

Font styles to use
Sans Serif
Script

Requirements
Must have
• Contact form, Mobile friendly, sitemap
Nice to have
• I really like the look for the sites I have included on the project description guide.
Should not have
• Nothing overly girly.

```html
<!DOCTYPE html>
<html lang="en">
<head>
<meta charset="utf-8">
<title>Brightcomb Studio – Hair and Makeup</title>
<link href="https://fonts.googleapis.com/css2?family=Great+Vibes&family=Raleway:wght@300;400;500;600&family=Open+Sans:wght@400;600&display=swap" rel="stylesheet">
<style>
  :root {
    --navy: #0d2a5c;
    --navy-deep: #0a1f45;
    --royal: #1d4aa8;
    --ink: #1c2540;
    --text: #2c2c3a;
    --peach: #f6c9a8;
    --rose: #ef9fae;
    --blush: #f8dfe0;
    --cream: #fdf3ea;
    --lilac: #e7c6e4;
    --footer: #1e2a33;
    --white: #ffffff;
  }
  * { box-sizing: border-box; margin: 0; padding: 0; }
  html, body { width: 1200px; height: 2604px; overflow: hidden; }
  body {
    position: relative;
    font-family: "Open Sans", Arial, sans-serif;
    color: var(--text);
    background:
      radial-gradient(ellipse 500px 700px at 1050px 1450px, rgba(239,120,150,.55), transparent 70%),
      radial-gradient(ellipse 600px 500px at 150px 500px, rgba(246,180,150,.55), transparent 70%),
      radial-gradient(ellipse 500px 500px at 900px 250px, rgba(231,198,228,.6), transparent 70%),
      radial-gradient(ellipse 600px 600px at 200px 2000px, rgba(246,190,160,.5), transparent 70%),
      radial-gradient(ellipse 500px 500px at 1000px 2200px, rgba(239,159,174,.45), transparent 70%),
      linear-gradient(180deg, var(--cream), var(--blush) 40%, #f9e4d6 70%, var(--blush));
  }
  .abs { position: absolute; }

  .brand { left: 0; width: 1200px; top: 60px; text-align: center; }
  .brand-mark { display: inline-flex; align-items: center; gap: 14px; }
  .brand-dot { width: 22px; height: 22px; border-radius: 50%; background: var(--navy); }
  .brand-name { font-family: "Raleway", sans-serif; font-weight: 500; font-size: 46px; color: var(--navy); }

  .nav { left: 40px; top: 232px; width: 1120px; height: 80px; }
  .nav svg { position: absolute; inset: 0; }
  .nav ul { position: absolute; left: 0; right: 0; top: 24px; display: flex; justify-content: center; gap: 110px; list-style: none; }
  .nav li { font-family: "Raleway", sans-serif; font-size: 22px; color: var(--white); letter-spacing: 1px; }

  .hero { left: 100px; top: 312px; width: 1000px; height: 456px; border-radius: 0 0 22px 22px;
    background: linear-gradient(90deg, #cfd4cf 0%, #e9e4dc 30%, #c8875f 55%, #8a4a2e 75%, #e8dccf 100%); }

  .script-title { left: 0; width: 1200px; text-align: center; color: var(--ink); }
  .script-title .script { font-family: "Great Vibes", cursive; font-size: 60px; }
  .script-title .sans { font-family: "Raleway", sans-serif; font-weight: 400; font-size: 54px; }

  .welcome-photo { left: 150px; top: 790px; width: 170px; height: 310px; border-radius: 40% 40% 8px 8px;
    background: linear-gradient(180deg, #d9a47c, #f3e2d6 55%, #e7a6b6); }
  .welcome-text { left: 370px; top: 892px; width: 560px; text-align: center; font-size: 16.5px; line-height: 1.5; color: var(--text); }

  .btn { display: inline-block; background: var(--navy); color: var(--white); font-family: "Raleway", sans-serif;
    border-radius: 30px; border: 2px solid #3b6fd0; text-align: center; }
  .btn-read { left: 530px; top: 1000px; width: 140px; height: 40px; line-height: 36px; font-size: 17px; }

  .divider { left: 180px; width: 840px; height: 4px; background: linear-gradient(90deg, transparent, var(--navy) 20%, var(--navy) 80%, transparent); opacity: .85; }

  .service { width: 320px; text-align: center; }
  .service-frame { width: 240px; height: 240px; margin: 0 auto; border-radius: 50%; border: 10px solid var(--navy);
    box-shadow: 0 0 0 6px rgba(29,74,168,.35); }
  .service h3 { margin-top: 48px; font-family: "Raleway", sans-serif; font-weight: 500; font-size: 32px; color: var(--ink); }
  .service p { margin-top: 12px; font-size: 16px; line-height: 1.45; }
  .btn-services { left: 490px; top: 1706px; width: 220px; height: 52px; line-height: 48px; font-size: 22px; }
  .rings { left: 950px; top: 1680px; width: 160px; height: 120px; border-radius: 50%;
    background: radial-gradient(circle, #f2d47a, #c99a3a 60%, transparent 72%); }

  .gallery-item { top: 1948px; height: 152px; width: 224px; }
  .arrow { top: 1990px; }

  .field { top: 2288px; width: 232px; height: 40px; background: var(--white); border: 1.5px solid var(--navy);
    font-size: 15px; padding: 10px 12px; color: #555; }
  .btn-contact { left: 510px; top: 2360px; width: 180px; height: 52px; line-height: 48px; font-size: 22px; }

  .footer { left: 0; top: 2460px; width: 1200px; height: 144px; background: var(--footer); color: var(--white); }
  .footer-nav { position: absolute; left: 80px; top: 38px; display: flex; gap: 34px; list-style: none;
    font-family: "Raleway", sans-serif; font-size: 21px; }
  .footer-copy { position: absolute; left: 80px; top: 88px; font-size: 15px; }
  .social { position: absolute; top: 44px; width: 52px; height: 52px; border-radius: 50%; border: 2px solid #4a78d0; background: var(--navy); }
</style>
</head>
<body>

<header>
  <div class="abs brand"><span class="brand-mark"><span class="brand-dot"></span><span class="brand-name">Brightcomb Studio</span></span></div>
  <nav class="abs nav">
    <svg width="1120" height="80" viewBox="0 0 1120 80">
      <path d="M0 10 L70 10 L55 40 L70 70 L0 70 Z" fill="var(--navy-deep)"/>
      <path d="M1120 10 L1050 10 L1065 40 L1050 70 L1120 70 Z" fill="var(--navy-deep)"/>
      <rect x="40" y="4" width="1040" height="72" rx="4" fill="var(--navy)"/>
      <rect x="48" y="10" width="1024" height="60" fill="none" stroke="#3b6fd0" stroke-width="1.5" stroke-dasharray="4 4"/>
    </svg>
    <ul><li>HOME</li><li>ABOUT</li><li>GALLERY</li><li>SERVICES</li><li>CONTACT</li></ul>
  </nav>
  <div class="abs hero" role="img" aria-label="Bridal bouquet beside a smiling bride with long auburn hair"></div>
</header>

<section class="welcome">
  <h2 class="abs script-title" style="top:812px"><span class="script">Welcome to </span><span class="sans" style="font-size:46px">Brightcomb Studio</span></h2>
  <div class="abs welcome-photo" role="img" aria-label="Bride holding a pink bouquet"></div>
  <p class="abs welcome-text">Brightcomb Studio specializes in providing gorgeous, long lasting hair and makeup. With over nine years of experience and training, we know how to make your day the very best! We take pride in client satisfaction.</p>
  <span class="abs btn btn-read">READ MORE</span>
</section>

<div class="abs divider" style="top:1098px"></div>

<section class="services">
  <h2 class="abs script-title" style="top:1146px"><span class="script">Lovely </span><span class="sans">Services</span></h2>
  <div class="abs service" style="left:60px;top:1260px">
    <div class="service-frame" role="img" aria-label="Bride with styled hair and veil" style="background:linear-gradient(160deg,#f4ede6,#d8b49a)"></div>
    <h3>Bridal</h3>
    <p>Lorem Ipsum is simply dummy text of the printing and typesetting industry. Lorem Ipsum has been the industry.</p>
  </div>
  <div class="abs service" style="left:440px;top:1260px">
    <div class="service-frame" role="img" aria-label="Woman with a fresh haircut in a yellow top" style="background:linear-gradient(160deg,#e8d37a,#8a5a3c)"></div>
    <h3>Hair Cut</h3>
    <p>Lorem Ipsum is simply dummy text of the printing and typesetting industry. Lorem Ipsum has been the industry.</p>
  </div>
  <div class="abs service" style="left:820px;top:1260px">
    <div class="service-frame" role="img" aria-label="Stylist treating a client's hair" style="background:linear-gradient(160deg,#c9c2c4,#6b4a3e)"></div>
    <h3>Styling &amp;Treatments</h3>
    <p>Lorem Ipsum is simply dummy text of the printing and typesetting industry. Lorem Ipsum has been the industry.</p>
  </div>
  <span class="abs btn btn-services">View All Service</span>
  <div class="abs rings" role="img" aria-label="Pair of gold wedding rings"></div>
</section>

<div class="abs divider" style="top:1798px"></div>

<section class="gallery">
  <h2 class="abs script-title" style="top:1844px"><span class="script">Lovely </span><span class="sans">Gallery</span></h2>
  <svg class="abs arrow" style="left:40px" width="24" height="44" viewBox="0 0 24 44"><path d="M20 4 L4 22 L20 40" fill="none" stroke="var(--navy)" stroke-width="3"/></svg>
  <div class="abs gallery-item" style="left:88px;background:linear-gradient(135deg,#e9e2dc,#6b4a3e)" role="img" aria-label="Stylist working on a client's hair"></div>
  <div class="abs gallery-item" style="left:352px;background:linear-gradient(135deg,#a7b08a,#d6b074)" role="img" aria-label="Portrait of a woman outdoors"></div>
  <div class="abs gallery-item" style="left:620px;background:linear-gradient(135deg,#3a3a3a,#d9d9d9)" role="img" aria-label="Black and white wedding photograph"></div>
  <div class="abs gallery-item" style="left:888px;width:232px;background:linear-gradient(135deg,#f1ece8,#7b8aa5)" role="img" aria-label="Bride and groom on their wedding day"></div>
  <svg class="abs arrow" style="left:1136px" width="24" height="44" viewBox="0 0 24 44"><path d="M4 4 L20 22 L4 40" fill="none" stroke="var(--navy)" stroke-width="3"/></svg>
</section>

<div class="abs divider" style="top:2158px"></div>

<section class="contact">
  <h2 class="abs script-title" style="top:2194px"><span class="script">Lovely </span><span class="sans">Contact</span></h2>
  <div class="abs field" style="left:88px">Enter Name</div>
  <div class="abs field" style="left:360px">Enter Email</div>
  <div class="abs field" style="left:628px">Enter Contact No.</div>
  <div class="abs field" style="left:888px">Enter Message</div>
  <span class="abs btn btn-contact">Contact Us</span>
</section>

<footer class="abs footer">
  <ul class="footer-nav"><li>HOME</li><li>ABOUT</li><li>GALLERY</li><li>SERVICES</li><li>CONTACT</li></ul>
  <p class="footer-copy">© <strong>Brightcomb Studio</strong> - 2015. All Rights Reserved.</p>
  <span class="social" style="left:894px"></span>
  <span class="social" style="left:982px"></span>
  <span class="social" style="left:1066px"></span>
</footer>

</body>
</html>
```